Dietitian/Nutritionist seeks trifold marketing brochure

We need a trifold brochure for marketing to patients within a doctors surgery. This will be a source of information for prospective patients, what they can expect and how to contact us. The brochure needs to have some key information such as a brief description of the services available, fees, locations of clinics and contact information. Our current brochure has been uploaded which has the information you need to complete this project. The files you provide will allow us to edit the information at a later date as pricing and services change.

Target Market(s)

Patients who have been referred to see a dietitian/nutritionist and people who are considering seeing a dietitian/nutritionist but haven't decided

Industry/Entity Type

Dietician

Font styles to use
Serif

Colors

Designer to choose colors to be used in the design.

Requirements
Must have
• My logo
• Accredited practising dietitian logo
• My website address and contact details
• Most of the information that is in my current brochure
• Locations/names of the four clinics
Nice to have
• Images that promote cooking, health and wellbeing

```html
<!DOCTYPE html>
<html lang="en">
<head>
<meta charset="utf-8">
<title>Eastvale Nutrition &amp; Dietetics – Trifold Brochure</title>
<link href="https://fonts.googleapis.com/css2?family=Open+Sans:wght@400;600&family=Kaushan+Script&display=swap" rel="stylesheet">
<style>
  :root{
    --navy:#1b2a8f;
    --blue:#1e73d8;
    --sky:#2aa3ef;
    --green:#6dbb2a;
    --green-dark:#4f9a1a;
    --orange:#f37a1f;
    --ink:#2b2b2b;
    --grey:#555;
    --page:#e9ebee;
  }
  *{box-sizing:border-box;margin:0;padding:0}
  html,body{width:828px;height:1200px;overflow:hidden;background:var(--page)}
  body{font-family:"Open Sans",Arial,sans-serif;color:var(--ink)}
  .stage{position:absolute;left:0;top:0;width:1000px;height:1450px;transform:scale(.828);transform-origin:0 0}
  .sheet{position:absolute;left:62px;width:876px;height:618px;background:#fff;overflow:hidden;box-shadow:0 6px 18px rgba(0,0,0,.25)}
  .sheet--outside{top:80px;background:linear-gradient(90deg,#fff 0 33.3%,#f7f9fb 33.3% 66.6%,#eef6fb 66.6%)}
  .sheet--inside{top:780px;background:linear-gradient(90deg,#fdf6ef 0 33.3%,#fffaf3 33.3% 66.6%,#fdf1ee 66.6%)}
  .fold{position:absolute;top:0;bottom:0;width:1px;background:rgba(0,0,0,.06)}
  .waves{position:absolute;left:0;top:0;width:876px;height:618px}
  .abs{position:absolute}
  .photo{position:absolute;border-radius:40% 45% 35% 40%}

  .lead{font-size:15px;line-height:20px}
  .services{list-style:none;margin-top:12px}
  .services li{position:relative;padding-left:20px;font-size:12.5px;line-height:17px;color:var(--grey);margin-bottom:3px}
  .services li::before{content:"";position:absolute;left:0;top:3px;width:11px;height:11px;border-radius:50%;background:conic-gradient(var(--green) 0 50%,var(--blue) 50%)}
  .services b{font-weight:400;color:var(--navy)}
  .web{font-size:13px;color:var(--navy);display:flex;align-items:center;gap:6px}
  .web svg{width:12px;height:12px}

  .intro{font-size:15px;line-height:20px;text-align:center;color:var(--ink)}
  .badge{background:var(--orange);border-radius:3px}
  .badge__disc{position:absolute;right:12px;top:12px;width:62px;height:62px;border-radius:50%;background:#fff}
  .together{font-size:15px;line-height:20px;text-align:center;color:var(--blue)}

  .brand{display:flex;align-items:center;gap:8px;color:var(--navy);font-weight:600}
  .brand__dot{width:40px;height:40px;border-radius:50%;background:var(--green);flex:none}
  .brand__name{font-size:30px;line-height:30px}
  .brand__sub{font-size:14px;line-height:16px}
  .contact{text-align:center;color:#fff}
  .contact__name{font-family:"Kaushan Script",cursive;font-size:25px;color:#111}
  .contact__role{font-size:15px;color:#1a1a1a;margin-top:2px}
  .contact__phone{font-size:18px;color:var(--navy);font-weight:600;margin-top:8px;display:flex;justify-content:center;gap:8px;align-items:center}
  .contact__line{font-size:13.5px;color:var(--navy);margin-top:6px;display:flex;justify-content:center;gap:6px;align-items:center}

  .body-text{font-size:11.6px;line-height:15.6px;text-align:justify;color:#222}
  .body-text strong{font-weight:600;color:var(--navy);display:block;font-size:13px}
  .locations-title{border:1px solid var(--navy);font-size:15px;color:var(--green-dark);padding:2px 10px;display:inline-flex;gap:6px;align-items:center}
  .locations{margin-top:14px;font-size:12.8px;line-height:19px}
  .locations b{font-weight:600;color:var(--navy)}

  .fees-tag{background:var(--green);color:#fff;font-size:17px;padding:4px 0 0 30px}
  .fees h3{font-size:12px;font-weight:600;color:var(--navy);margin-top:10px}
  .fees p{font-size:9.5px;line-height:13px;color:#666;margin-top:4px}
  .fees .fee{font-size:12px;color:#222;line-height:17px}
  .fees .fee span{color:var(--navy);font-size:14px;font-weight:600}
  .fees p em{font-style:normal;color:var(--navy);font-size:12.5px;font-weight:600}
</style>
</head>
<body>
<main class="stage">

  <!-- Outside spread -->
  <section class="sheet sheet--outside">
    <svg class="waves" viewBox="0 0 876 618" aria-hidden="true">
      <defs>
        <linearGradient id="swoosh" x1="0" x2="1"><stop offset="0" stop-color="#1b2a8f"/><stop offset=".55" stop-color="#1e73d8"/><stop offset="1" stop-color="#2aa3ef"/></linearGradient>
      </defs>
      <path d="M0,440 C180,560 330,600 480,585 C640,570 760,470 876,420 L876,618 L0,618Z" fill="url(#swoosh)"/>
      <path d="M0,465 C180,575 330,612 480,598 C640,585 760,490 876,450 L876,618 L0,618Z" fill="#fff"/>
      <path d="M0,500 C180,585 330,620 480,600 C640,582 760,505 876,470 L876,618 L0,618Z" fill="#6dbb2a"/>
    </svg>
    <div class="fold" style="left:292px"></div>
    <div class="fold" style="left:584px"></div>

    <div class="abs" style="left:30px;top:22px;width:250px">
      <p class="lead">An Accredited Practising Dietitian can assist you with:</p>
      <ul class="services">
        <li><b>Diabetes –</b> Impaired Glucose Tolerance, Type 1 &amp; 2 Diabetes, Gestational Diabetes</li>
        <li><b>Digestive Health –</b> Irritable Bowel Syndrome, Coeliac Disease, Diverticular Disease</li>
        <li><b>Gastric banding</b> and other surgical methods of weight loss</li>
        <li><b>Cardiovascular</b> - High cholesterol, High Blood Pressure, Risk Reduction</li>
        <li><b>Weight Management –</b> loss/gain and support</li>
        <li><b>General</b> Healthy Eating &amp;Nutrition</li>
      </ul>
    </div>
    <div class="photo" role="img" aria-label="Photo of fresh blackberries, raspberries and blueberries" style="left:68px;top:372px;width:200px;height:150px;background:radial-gradient(circle at 45% 45%,#c0304a,#3a2a55 55%,rgba(90,110,160,.0) 75%)"></div>
    <p class="web abs" style="left:34px;top:588px"><svg viewBox="0 0 12 12"><circle cx="6" cy="6" r="5" fill="none" stroke="#222"/><path d="M1 6h10M6 1c-3 3-3 7 0 10M6 1c3 3 3 7 0 10" fill="none" stroke="#222" stroke-width=".8"/></svg>www.valleydietitian.example</p>

    <p class="intro abs" style="left:312px;top:22px;width:252px">Helping you to meet your individual nutrition goals with an emphasis on practical skills, everyday foods, and providing you with up to date advice.</p>
    <div class="badge abs" role="img" aria-label="Accredited practising dietitian badge" style="left:347px;top:137px;width:182px;height:86px"><span class="badge__disc"></span></div>
    <p class="together abs" style="left:312px;top:240px;width:252px">We work together to develop personalised eating plans that take</p>
    <div class="photo" role="img" aria-label="Photo of a glass of carrot juice surrounded by apples, apricots, kiwi and berries" style="left:300px;top:300px;width:275px;height:215px;background:radial-gradient(ellipse at 50% 55%,#e8682a,#c8d23a 45%,#b81f30 65%,rgba(255,255,255,0) 78%)"></div>
    <p class="web abs" style="left:326px;top:588px"><svg viewBox="0 0 12 12"><circle cx="6" cy="6" r="5" fill="none" stroke="#222"/><path d="M1 6h10M6 1c-3 3-3 7 0 10M6 1c3 3 3 7 0 10" fill="none" stroke="#222" stroke-width=".8"/></svg>www.valleydietitian.example</p>

    <div class="brand abs" style="left:622px;top:24px">
      <span class="brand__dot"></span>
      <div><div class="brand__name">Eastvale</div><div class="brand__sub">Nutrition &amp; Dietetics</div></div>
    </div>
    <div class="photo" role="img" aria-label="Photo of mint leaves with raspberries, blackberries and blueberries" style="left:585px;top:110px;width:280px;height:285px;background:radial-gradient(circle at 50% 55%,#3d3a70,#b8304a 35%,#7cbf3a 58%,rgba(255,255,255,0) 75%)"></div>
    <div class="contact abs" style="left:584px;top:475px;width:292px">
      <div class="contact__name">Daniel Ashworth</div>
      <div class="contact__role">Accredited Practising Dietitian &amp; Chef</div>
      <div class="contact__phone"><svg width="16" height="16" viewBox="0 0 16 16"><circle cx="8" cy="8" r="7" fill="none" stroke="#111"/><path d="M5.5 4.5l1.5 1.5-1 1c.6 1.3 1.5 2.2 2.8 2.8l1-1 1.5 1.5-1 1.2C7.5 11.3 4.7 8.5 4.4 5.6z" fill="#111"/></svg>0400 123 456</div>
      <div class="contact__line"><svg width="12" height="9" viewBox="0 0 12 9"><rect x=".5" y=".5" width="11" height="8" fill="none" stroke="#222"/><path d="M.5.5l5.5 4.5 5.5-4.5" fill="none" stroke="#222"/></svg>daniel.a.nutrition@example.com</div>
      <div class="contact__line"><svg width="12" height="12" viewBox="0 0 12 12"><circle cx="6" cy="6" r="5" fill="none" stroke="#222"/><path d="M1 6h10M6 1c-3 3-3 7 0 10M6 1c3 3 3 7 0 10" fill="none" stroke="#222" stroke-width=".8"/></svg>www.valleydietitian.example</div>
    </div>
  </section>

  <!-- Inside spread -->
  <section class="sheet sheet--inside">
    <svg class="waves" viewBox="0 0 876 618" aria-hidden="true">
      <defs>
        <linearGradient id="swoosh2" x1="0" x2="1"><stop offset="0" stop-color="#1e73d8"/><stop offset=".5" stop-color="#1b2a8f"/><stop offset="1" stop-color="#2aa3ef"/></linearGradient>
      </defs>
      <path d="M0,365 C200,470 500,540 876,445 L876,618 L0,618Z" fill="url(#swoosh2)"/>
      <path d="M0,385 C200,490 500,555 876,462 L876,618 L0,618Z" fill="#fff"/>
      <path d="M0,410 C200,505 500,565 876,478 L876,618 L0,618Z" fill="#6dbb2a"/>
    </svg>
    <div class="fold" style="left:292px"></div>
    <div class="fold" style="left:584px"></div>

    <p class="body-text abs" style="left:30px;top:24px;width:235px"><strong>Accredited Practising Dietitians (APDs)</strong>are university trained experts in food and nutrition, they are able to translate the latest scientific evidence into sensible and practical advice. Dietitians differ from nutritionists as they have specific training in clinical environments such as hospitals. This training allows a dietitian to interpret blood tests, understand any food and medication interactions, and communicate with other health professionals involved in your care.</p>
    <div class="abs" role="img" aria-label="Illustration of a hanging sign reading good health" style="left:45px;top:225px;width:185px;height:150px;background:linear-gradient(160deg,#2f7fe0,#1b2a8f);border-radius:8px;transform:rotate(-8deg);clip-path:polygon(0 30%,100% 15%,100% 100%,0 100%)"></div>
    <svg class="abs" style="left:20px;top:375px" width="220" height="220" aria-hidden="true"><circle cx="110" cy="110" r="104" fill="#fff" stroke="#1b2a8f" stroke-width="9"/></svg>
    <div class="abs" role="img" aria-label="Photo of a wicker basket full of strawberries and mixed berries" style="left:40px;top:395px;width:180px;height:180px;border-radius:50%;background:radial-gradient(circle,#d8302e,#7a1f3a 45%,#c89a5a 62%,#fff 72%)"></div>

    <p class="body-text abs" style="left:318px;top:24px;width:242px">Seeing a dietitian for the first time involves working with you to develop strategies and goals to improve your health. Follow up visits are recommended to monitor your progress and may include more measurements and new strategies to help YOU realise your goals. Every person is unique and I can</p>
    <div class="abs" style="left:318px;top:152px;width:250px">
      <div class="locations-title"><svg width="9" height="14" viewBox="0 0 9 14"><circle cx="4.5" cy="4" r="3" fill="none" stroke="#1b2a8f" stroke-width="1.5"/><path d="M4.5 7v6M1.5 13h6" stroke="#1b2a8f" stroke-width="1.5"/></svg>Locations</div>
      <div class="locations">
        <div><b>Hillcrest Medical Centre</b></div>
        <div>Northgate - Fridays</div>
        <div><b>Brookfield Medical</b> - Wednesdays</div>
        <div><b>Westbank Health</b> Eastbrook –Thursdays</div>
        <div><b>Ridgeway Doctors Surgery –</b></div>
        <div>Approximately every 4 weeks</div>
      </div>
    </div>
    <div class="photo" role="img" aria-label="Photo of orange and grapefruit juices with citrus, cucumber, strawberries, kiwi and tomato" style="left:270px;top:330px;width:560px;height:220px;background:radial-gradient(ellipse at 45% 50%,#f5a623,#ef6a3a 40%,#8ac23c 60%,rgba(255,255,255,0) 75%)"></div>
    <p class="web abs" style="left:326px;top:588px"><svg viewBox="0 0 12 12"><circle cx="6" cy="6" r="5" fill="none" stroke="#222"/><path d="M1 6h10M6 1c-3 3-3 7 0 10M6 1c3 3 3 7 0 10" fill="none" stroke="#222" stroke-width=".8"/></svg>www.valleydietitian.example</p>

    <div class="abs fees" style="left:610px;top:0;width:250px">
      <div class="fees-tag" style="width:102px;height:34px">FEES</div>
      <h3>Chronic Disease Management Plans</h3>
      <p>If your Doctor has referred you with a Chronic Disease Management Plan to assist in the ongoing management of your health condition you are eligible for a rebate of <em>$52.95 from Medicare.</em></p>
      <h3 style="font-weight:400;font-size:11px">All Fees are payable on the day Private Patients</h3>
      <div class="fee" style="margin-top:6px">Initial Consultation<br><span>(60mins) $120</span></div>
      <div class="fee">Follow up Consultation <span>(30mins) $65</span></div>
      <h3 style="margin-top:6px">Private Health Funds</h3>
      <p>Rebates are available through most private health funds but rates vary depending on your level of cover. Check with your fund directly to find outmore. Payment is required on the day of your consultation</p>
    </div>
    <div class="brand abs" style="left:660px;top:305px">
      <span class="brand__dot"></span>
      <div><div class="brand__name">Eastvale</div><div class="brand__sub">Nutrition &amp; Dietetics</div></div>
    </div>
    <svg class="abs" style="left:710px;top:455px" width="140" height="140" aria-hidden="true"><circle cx="70" cy="70" r="65" fill="#fff" stroke="#1b2a8f" stroke-width="7"/></svg>
    <div class="abs" role="img" aria-label="Photo of green and red apples" style="left:725px;top:470px;width:110px;height:110px;border-radius:50%;background:radial-gradient(circle at 40% 55%,#9fd34a,#6dae2a 45%,#d5302a 62%,#fff 75%)"></div>
  </section>

</main>
</body>
</html>
```